PHD-project

i need the figures to be in the same stile. info is inside the file. There are 5 figures that need redesign. this is for PhD.

Target Market(s)

it will be used in my phd

Colors

```html
<!DOCTYPE html>
<html lang="en">
<head>
<meta charset="UTF-8">
<title>Design Thinking</title>
<link rel="stylesheet" href="https://fonts.googleapis.com/css2?family=Montserrat:wght@700&family=Urbanist:wght@100;400&display=swap">
<style>
  :root {
    --paper: #ffffff;
    --ink: #111111;
    --label: #ffffff;
    --word-mark: rgba(255, 255, 255, 0.55);
    --analytic-light: #74e6f9;
    --analytic-mid: #4cc0f2;
    --analytic-edge: #2f86d8;
    --creative-light: #a3e8e4;
    --creative-mid: #3fb8b4;
    --creative-edge: #0a8785;
    --overlap-light: #0a95c9;
    --overlap-deep: #173f90;
    --track-left: #3a8fd0;
    --track-mid: #0b2761;
    --track-right: #1f968c;
  }
  html, body {
    margin: 0;
    padding: 0;
    overflow: hidden;
    background: var(--paper);
  }
  .canvas {
    position: relative;
    width: 1200px;
    height: 780px;
    background: var(--paper);
    overflow: hidden;
  }
  .diagram {
    position: absolute;
    inset: 0;
  }
  .zone-label {
    font-family: "Montserrat", sans-serif;
    font-weight: 700;
    font-size: 30px;
    fill: var(--label);
  }
  .word-mark {
    font-family: "Urbanist", sans-serif;
    font-weight: 100;
    font-size: 84px;
    letter-spacing: 1px;
    fill: var(--word-mark);
  }
  .stage-label {
    font-family: "Urbanist", sans-serif;
    font-weight: 400;
    font-size: 27px;
    letter-spacing: 1px;
    fill: var(--ink);
  }
</style>
</head>
<body>
<main class="canvas">
  <svg class="diagram" width="1200" height="780" viewBox="0 0 1200 780" role="img" aria-label="Design thinking: overlap of analytic and intuitive and creative thinking, moving between understanding the problem and designing the solution">
    <defs>
      <radialGradient id="analyticFill" cx="400" cy="320" r="300" gradientUnits="userSpaceOnUse">
        <stop offset="0" stop-color="var(--analytic-light)"/>
        <stop offset="0.6" stop-color="var(--analytic-mid)"/>
        <stop offset="1" stop-color="var(--analytic-edge)"/>
      </radialGradient>
      <radialGradient id="creativeFill" cx="685" cy="320" r="300" gradientUnits="userSpaceOnUse">
        <stop offset="0" stop-color="var(--creative-light)"/>
        <stop offset="0.55" stop-color="var(--creative-mid)"/>
        <stop offset="1" stop-color="var(--creative-edge)"/>
      </radialGradient>
      <linearGradient id="creativeTop" x1="0" y1="238" x2="0" y2="330" gradientUnits="userSpaceOnUse">
        <stop offset="0" stop-color="#1ee3e3" stop-opacity="0.9"/>
        <stop offset="1" stop-color="#1ee3e3" stop-opacity="0"/>
      </linearGradient>
      <linearGradient id="overlapFill" x1="520" y1="460" x2="690" y2="320" gradientUnits="userSpaceOnUse">
        <stop offset="0" stop-color="var(--overlap-light)"/>
        <stop offset="1" stop-color="var(--overlap-deep)"/>
      </linearGradient>
      <linearGradient id="trackFill" x1="180" y1="0" x2="1020" y2="0" gradientUnits="userSpaceOnUse">
        <stop offset="0" stop-color="var(--track-left)"/>
        <stop offset="0.5" stop-color="var(--track-mid)"/>
        <stop offset="1" stop-color="var(--track-right)"/>
      </linearGradient>
      <linearGradient id="arrowFill" x1="528" y1="0" x2="672" y2="0" gradientUnits="userSpaceOnUse">
        <stop offset="0" stop-color="var(--track-left)"/>
        <stop offset="0.5" stop-color="var(--track-mid)"/>
        <stop offset="1" stop-color="var(--track-right)"/>
      </linearGradient>
      <clipPath id="aboveTrack">
        <rect x="0" y="0" width="1200" height="483"/>
      </clipPath>
      <clipPath id="analyticShape">
        <circle cx="464" cy="463" r="225"/>
      </clipPath>
    </defs>

    <g class="domes" clip-path="url(#aboveTrack)">
      <circle class="dome dome--analytic" cx="464" cy="463" r="225" fill="url(#analyticFill)"/>
      <circle class="dome dome--creative" cx="736" cy="463" r="225" fill="url(#creativeFill)"/>
      <circle class="dome dome--creative-glow" cx="736" cy="463" r="225" fill="url(#creativeTop)"/>
      <g clip-path="url(#analyticShape)">
        <circle class="dome dome--overlap" cx="736" cy="463" r="225" fill="url(#overlapFill)"/>
      </g>
    </g>

    <text class="word-mark" x="398" y="482">THINKING</text>

    <rect class="track" x="180" y="482" width="840" height="7" fill="url(#trackFill)"/>

    <text class="zone-label" x="356" y="378">Analytic</text>
    <text class="zone-label" x="544" y="378">Design</text>
    <text class="zone-label" x="698" y="378">Intuitive &amp;</text>
    <text class="zone-label" x="898" y="409" text-anchor="end">Creative</text>

    <text class="stage-label" x="504" y="551" text-anchor="end">Understand</text>
    <text class="stage-label" x="504" y="581" text-anchor="end">Problem</text>

    <path class="stage-arrow" d="M528 554 L552 540 L552 549 L648 549 L648 540 L672 554 L648 568 L648 559 L552 559 L552 568 Z" fill="url(#arrowFill)"/>

    <text class="stage-label" x="698" y="551">Design</text>
    <text class="stage-label" x="698" y="581">Solution</text>
  </svg>
</main>
</body>
</html>
```